Business Card Design for BrightvaleMedia.com

--I need a business card design for my company BrightvaleMedia.com

I have attached my logo...I want the brightvale media logo on the front of the business card, and then I want The Quillstone Chief on the back of it with my information.

I would like to see a light colored background as well as a dark colored background

FRONT:
BRIGHTVALE MEDIA LOGO
248 N. Larkmoor
3rd Floor
San Diego CA 92173
www.BrightvaleMedia.com

Advanced Website & App Development
Websites, Apps, Online Voucher Systems

Leading Edge Marketing Services
SMS, VB, SMM, SEM,

BACK:
QUILLSTONE CHIEF LOGO
Dorian Pelletta
The Quillstone Chief
Call Or Text: 619-555-0148
Dorian@QuillstoneChief.example
www.QuillstoneChief.example

Target Market(s)

small business owners

Industry/Entity Type

Business Consultant

Contact Information for Business Card

FRONT:
BRIGHTVALE MEDIA LOGO
248 N. Larkmoor
3rd Floor
San Diego CA 92173
www.BrightvaleMedia.com

SMS, VB, SMM, SEM,

BACK:
QUILLSTONE CHIEF LOGO
Dorian Pelletta
The Quillstone Chief
Dorian@QuillstoneChief.example
www.QuillstoneChief.example

Requirements
Must have
• add this quote on it somewhere, anywhere,preferrably on back
• "The Fastest Way To Success Is To Take Action”
• — Dorian Pelletta, Quillstone Chief
Nice to have
• open
Should not have
• red

```html
<!DOCTYPE html>
<html lang="en">
<head>
<meta charset="utf-8">
<title>Brightvale Media Business Cards</title>
<link href="https://fonts.googleapis.com/css2?family=Jura:wght@400;500;600;700&display=swap" rel="stylesheet">
<style>
  :root {
    --brand-blue: #1b6dab;
    --ink: #1e1e1e;
    --slate: #5a5a5a;
    --paper: #ffffff;
    --backdrop: #e4e6e8;
  }
  * { box-sizing: border-box; margin: 0; padding: 0; }
  html, body { width: 1200px; height: 900px; overflow: hidden; }
  body {
    background: var(--backdrop);
    font-family: "Jura", sans-serif;
    color: var(--ink);
    position: relative;
  }
  .card {
    position: absolute;
    left: 280px;
    width: 640px;
    height: 366px;
    background: var(--paper);
    box-shadow: 0 6px 18px rgba(0,0,0,.18);
    overflow: hidden;
  }
  .card--chief { top: 60px; }
  .card--company { top: 474px; }

  .band {
    position: absolute;
    left: 0; right: 0;
    background: var(--brand-blue);
    color: var(--paper);
    text-align: center;
    display: flex;
    flex-direction: column;
    justify-content: center;
  }

  /* Chief card */
  .chief-wordmark {
    position: absolute;
    top: 40px; left: 0; right: 0;
    text-align: center;
    font-size: 46px;
    font-weight: 700;
    letter-spacing: 2px;
    color: var(--brand-blue);
  }
  .band--quote { top: 118px; height: 62px; }
  .quote-text { font-size: 15px; font-style: italic; letter-spacing: .5px; }
  .quote-credit { font-size: 13px; letter-spacing: .5px; margin-top: 2px; }
  .contact {
    position: absolute;
    right: 30px; top: 200px;
    text-align: right;
  }
  .contact-name {
    font-size: 34px;
    font-weight: 600;
    color: var(--brand-blue);
    letter-spacing: 1px;
    line-height: 1;
  }
  .contact-title {
    font-size: 22px;
    color: var(--slate);
    letter-spacing: 1px;
    margin-bottom: 10px;
  }
  .contact-line {
    display: flex;
    justify-content: flex-end;
    align-items: center;
    gap: 8px;
    font-size: 18px;
    font-weight: 500;
    line-height: 26px;
  }
  .contact-line .accent { color: var(--brand-blue); }
  .contact-icon { width: 18px; height: 18px; flex: none; }

  /* Company card */
  .band--address { top: 26px; height: 70px; font-size: 19px; font-weight: 500; letter-spacing: 1px; line-height: 26px; }
  .company-web {
    position: absolute;
    top: 108px; left: 0; right: 0;
    text-align: center;
    font-size: 17px;
    font-weight: 600;
    letter-spacing: .5px;
    color: var(--slate);
  }
  .company-web .accent { color: var(--brand-blue); }
  .company-wordmark {
    position: absolute;
    top: 136px; left: 0; right: 0;
    text-align: center;
    font-size: 46px;
    font-weight: 700;
    letter-spacing: 2px;
    color: var(--brand-blue);
  }
  .band--services { top: 232px; height: 68px; font-size: 20px; font-weight: 600; letter-spacing: 1px; line-height: 27px; }
  .marketing-services {
    position: absolute;
    top: 308px; left: 0; right: 0;
    text-align: center;
    font-size: 20px;
    font-weight: 600;
    letter-spacing: 1px;
    line-height: 25px;
  }
</style>
</head>
<body>

<section class="card card--chief" aria-label="Back of card">
  <div class="chief-wordmark">QUILLSTONE CHIEF</div>
  <div class="band band--quote">
    <p class="quote-text">“The Fastest Way To Success Is To Take Action”</p>
    <p class="quote-credit">— Dorian Pelletta, Quillstone Chief</p>
  </div>
  <div class="contact">
    <p class="contact-name">DORIAN PELLETTA</p>
    <p class="contact-title">The Quillstone Chief</p>
    <p class="contact-line">619-555-0148
      <svg class="contact-icon" viewBox="0 0 18 18" aria-hidden="true"><circle cx="9" cy="9" r="9" fill="#1b6dab"/><rect x="6" y="4" width="6" height="10" rx="1.2" fill="none" stroke="#fff" stroke-width="1.3"/></svg>
    </p>
    <p class="contact-line">Dorian@QuillstoneChief.example
      <svg class="contact-icon" viewBox="0 0 18 18" aria-hidden="true"><circle cx="9" cy="9" r="9" fill="#1b6dab"/><rect x="4.5" y="5.5" width="9" height="7" fill="none" stroke="#fff" stroke-width="1.2"/><path d="M4.5 5.5 L9 9.5 L13.5 5.5" fill="none" stroke="#fff" stroke-width="1.2"/></svg>
    </p>
    <p class="contact-line">www.<span class="accent">QuillstoneChief</span>.example
      <svg class="contact-icon" viewBox="0 0 18 18" aria-hidden="true"><circle cx="9" cy="9" r="9" fill="#1b6dab"/><circle cx="9" cy="9" r="5" fill="none" stroke="#fff" stroke-width="1.2"/><path d="M4 9 H14 M9 4 C6.5 6.5 6.5 11.5 9 14 M9 4 C11.5 6.5 11.5 11.5 9 14" fill="none" stroke="#fff" stroke-width="1"/></svg>
    </p>
  </div>
</section>

<section class="card card--company" aria-label="Front of card">
  <div class="band band--address">
    <p>248 N. Larkmoor, 3rd Floor</p>
    <p>San Diego CA 92173</p>
  </div>
  <p class="company-web">www.<span class="accent">BrightvaleMedia</span>.com</p>
  <div class="company-wordmark">BRIGHTVALE MEDIA</div>
  <div class="band band--services">
    <p>Advanced Website &amp; App Development</p>
    <p>Websites, Apps, Online Voucher Systems</p>
  </div>
  <div class="marketing-services">
    <p>Leading Edge Marketing Services</p>
    <p>SMS, VB, SMM, SEM,</p>
  </div>
</section>

</body>
</html>
```